Create Premium Wine Label Design

We are premium wine exporters from Australia. We are looking to introduce new brand " The Velmora" - in red wine, White wine and Sparkling wine to international market.

The sample label design for red wine ( Shiraz) is attached.

This is our luxury brand. We need a stunning wine label designs for (front, back and neck) that should be mostly in GOLD colour and design should be really eye catching.

We have provided sample design for front, back and neck labels. However, we are looking forward to see a completely new improvised design.

LOGO attached.

Front Label Design Specification:

* We would like to see designs that are in Gold colour.
* Wine Bottle size is standard: 750ml; we assume the same design can be resizable to different bottle sizes.
* Our design should suit both black, white and sparkling wine bottles(sample attached)
* Use our logo in the design (see attached - label sample)
* Content for front label (see attached).
* Design should include all information specified in the sample

Back Label Design
* All contents in the sample should be used ( sample attached)
* LOGO attached.

Neck Label Design
* Sample of Neck label attached, please provide similar or your own design.
* LOGO attached.

Image Samples:
* Samples of label designs we like (see attached)
* Sample for gold color (see attached)
* For bottle shapes (see attached)
* Front, Back and Neck Label Samples (see attached)

Target Market(s)

International Wine Market

Font styles to use
Decorative
Script

Requirements
Must have
• Must have golden color on front and back label

```html
<!DOCTYPE html>
<html lang="en">
<head>
<meta charset="utf-8">
<title>Southvale Shiraz Label Range</title>
<link rel="stylesheet" href="https://fonts.googleapis.com/css2?family=Cinzel:wght@600&family=Great+Vibes&family=Playfair+Display:wght@900&family=Oswald:wght@500&display=swap">
<style>
:root{
  --bg:#eeeeee;
  --gold-dark:#8a6a22;
  --gold:#d9b65a;
  --gold-light:#f6e39a;
  --gold-band:linear-gradient(180deg,#9c7a2c 0%,#e9cf7f 30%,#fbeeb4 50%,#d6b15a 75%,#9c7a2c 100%);
  --red:#5c1a1a;
  --red-deep:#3f0f10;
  --navy:#1c2e45;
  --navy-deep:#0f1c2c;
  --plum:#2e1838;
  --plum-deep:#130c1a;
  --seal:#c4161c;
  --seal-deep:#8e0d12;
  --ink:#4a1414;
}
*{box-sizing:border-box;margin:0;padding:0}
html,body{width:1110px;height:1200px;overflow:hidden;background:var(--bg)}
.canvas{position:relative;width:1110px;height:1200px;display:flex;justify-content:space-between;padding:110px 30px 0}
.variant{width:330px;display:flex;flex-direction:column;align-items:center}
.variant.red{--tone:var(--red);--tone-deep:var(--red-deep)}
.variant.white{--tone:var(--navy);--tone-deep:var(--navy-deep)}
.variant.sparkling{--tone:var(--plum);--tone-deep:var(--plum-deep)}

.neck-label{width:250px;height:86px;background:var(--tone);border-top:3px solid var(--gold);border-bottom:3px solid var(--gold);display:flex;flex-direction:column;align-items:center;justify-content:center;gap:6px}
.neck-brand{font:600 20px/1 'Cinzel',serif;color:var(--gold);letter-spacing:1px}
.flourish{display:block;border-radius:3px;background:linear-gradient(90deg,transparent,var(--gold) 30%,var(--gold-light) 50%,var(--gold) 70%,transparent)}
.neck-label .flourish{width:120px;height:8px}

.front-label{margin-top:54px;width:330px;height:820px;position:relative;border-radius:48% 48% 14% 14% / 13% 13% 5% 5%;background:linear-gradient(180deg,var(--tone) 0%,var(--tone) 60%,var(--tone-deep) 100%);border:5px solid var(--gold);box-shadow:0 0 0 2px var(--gold-dark) inset,0 0 0 9px var(--tone) inset,0 0 0 11px var(--gold) inset;display:flex;flex-direction:column;align-items:center;padding-top:40px;overflow:hidden}
.crest{width:90px;height:34px}
.brand{margin-top:40px;display:flex;align-items:center;gap:8px;font:600 29px/1 'Cinzel',serif;color:var(--gold);letter-spacing:1px}
.brand-dot{width:14px;height:14px;border-radius:50%;background:var(--gold)}
.brand-rule{margin-top:12px;width:150px;height:10px}

.variety-band{margin-top:36px;width:100%;height:230px;background:var(--gold-band);position:relative;display:flex;flex-direction:column;align-items:center;padding-top:22px}
.band-rule{width:150px;height:10px;background:linear-gradient(90deg,transparent,var(--ink) 30%,var(--ink) 70%,transparent);opacity:.7}
.variety{margin-top:8px;font:900 62px/1 'Playfair Display',serif;color:var(--ink);letter-spacing:-1px}

.seal{position:absolute;left:50%;top:120px;transform:translateX(-50%);width:150px;height:150px;border-radius:50%;background:radial-gradient(circle at 40% 35%,#e23a3a,var(--seal) 45%,var(--seal-deep) 100%);display:flex;align-items:center;justify-content:center}
.seal-plate{width:150px;height:38px;border:2px solid var(--gold);background:var(--seal-deep);border-radius:6px;display:flex;align-items:center;justify-content:center;font:600 17px/1 'Cinzel',serif;color:var(--gold-light)}

.wine-type{margin-top:92px;max-width:280px;white-space:nowrap;text-align:center;font:400 54px/1 'Great Vibes',cursive;color:var(--gold);word-spacing:4px}
.variant.sparkling .wine-type{font-size:44px;margin-top:98px}
.origin{margin-top:10px;font:500 11px/1 'Oswald',sans-serif;letter-spacing:4px;color:#e6d8b0}
.vintage-row{margin-top:30px;display:flex;align-items:center;gap:8px}
.vintage-row .flourish{width:40px;height:8px}
.vintage{width:96px;height:42px;border:2px solid var(--gold);border-radius:21px;background:var(--gold-band);display:flex;align-items:center;justify-content:center;font:500 26px/1 'Oswald',sans-serif;color:var(--ink)}
</style>
</head>
<body>
<main class="canvas">

  <section class="variant red">
    <div class="neck-label">
      <span class="neck-brand">SOUTHVALE</span>
      <span class="flourish" role="img" aria-label="Gold scroll ornament"></span>
    </div>
    <article class="front-label">
      <span class="flourish crest" role="img" aria-label="Gold crest ornament"></span>
      <div class="brand"><span class="brand-dot"></span>SOUTHVALE</div>
      <span class="flourish brand-rule" role="img" aria-label="Gold scroll ornament"></span>
      <div class="variety-band">
        <span class="band-rule" role="img" aria-label="Scroll ornament"></span>
        <h2 class="variety">SHIRAZ</h2>
        <div class="seal" role="img" aria-label="Red wax seal"><span class="seal-plate">The Velmora</span></div>
      </div>
      <p class="wine-type">Red Wine</p>
      <p class="origin">PREMIUM AUSTRALIAN</p>
      <div class="vintage-row"><span class="flourish" role="img" aria-label="Gold flourish"></span><span class="vintage">2018</span><span class="flourish" role="img" aria-label="Gold flourish"></span></div>
    </article>
  </section>

  <section class="variant white">
    <div class="neck-label">
      <span class="neck-brand">SOUTHVALE</span>
      <span class="flourish" role="img" aria-label="Gold scroll ornament"></span>
    </div>
    <article class="front-label">
      <span class="flourish crest" role="img" aria-label="Gold crest ornament"></span>
      <div class="brand"><span class="brand-dot"></span>SOUTHVALE</div>
      <span class="flourish brand-rule" role="img" aria-label="Gold scroll ornament"></span>
      <div class="variety-band">
        <span class="band-rule" role="img" aria-label="Scroll ornament"></span>
        <h2 class="variety">SHIRAZ</h2>
        <div class="seal" role="img" aria-label="Red wax seal"><span class="seal-plate">The Velmora</span></div>
      </div>
      <p class="wine-type">White Wine</p>
      <p class="origin">PREMIUM AUSTRALIAN</p>
      <div class="vintage-row"><span class="flourish" role="img" aria-label="Gold flourish"></span><span class="vintage">2018</span><span class="flourish" role="img" aria-label="Gold flourish"></span></div>
    </article>
  </section>

  <section class="variant sparkling">
    <div class="neck-label">
      <span class="neck-brand">SOUTHVALE</span>
      <span class="flourish" role="img" aria-label="Gold scroll ornament"></span>
    </div>
    <article class="front-label">
      <span class="flourish crest" role="img" aria-label="Gold crest ornament"></span>
      <div class="brand"><span class="brand-dot"></span>SOUTHVALE</div>
      <span class="flourish brand-rule" role="img" aria-label="Gold scroll ornament"></span>
      <div class="variety-band">
        <span class="band-rule" role="img" aria-label="Scroll ornament"></span>
        <h2 class="variety">SHIRAZ</h2>
        <div class="seal" role="img" aria-label="Red wax seal"><span class="seal-plate">The Velmora</span></div>
      </div>
      <p class="wine-type">Sparkling Wine</p>
      <p class="origin">PREMIUM AUSTRALIAN</p>
      <div class="vintage-row"><span class="flourish" role="img" aria-label="Gold flourish"></span><span class="vintage">2018</span><span class="flourish" role="img" aria-label="Gold flourish"></span></div>
    </article>
  </section>

</main>
</body>
</html>
```